Golf Course Membership Flyer

I am looking for a design for a double sided A5 flyer that will promote a variety of membership types that are playable either by weekly, fortnightly or monthly instillments. there are packages available from juniors to seniors and they cover playing once a week to 7 days per week. There is something for everyone. We would like to see the image attached used. Our website is www.thistlebankgolfpark.com.au
Updates

GuysI have updated some copy and membership details now and am adding some additional photos of the club i.e course, restaurant, changing rooms pro shop etc Added Tuesday, May 30, 2017

Target Market(s)

Primarily male but covers youth and female, regular golfers in Victoria Australia

Industry/Entity Type

Golf Course

Font styles to use
Sans Serif

Colors
acd036
faa54b
0592cd

Requirements
Must have
• Double sided A5. With Logo. (we will provide later.) must have ability to list multiple membership types. We are an award winning 18 hole golf course. we have just been voted 15th best value course in australia.
• see some other work we have had done http://thistlebank.fairwaydays.com.au/
Nice to have
• A table showing membership inclusions by membership type. The following text: New Golf Membership Passes
• The Thistle Bank is proud to launch its new 2017/18 golf membership pass. You can now enjoy golf all year round, at one of Australia’s leading courses and choose from a variety of pass options that suit every budget. The Thistle Bank boasts private club quality amenities yet remains a public course open to all and one where every visitor feels truly at home.
• For a tour, application form or to find out more call our membership co-ordinator on 03 9482 5160

```html
<!DOCTYPE html>
<html lang="en">
<head>
<meta charset="utf-8">
<title>Thistle Bank Golf Course – Membership Flyer</title>
<link href="https://fonts.googleapis.com/css2?family=Open+Sans:wght@400;600;700&display=swap" rel="stylesheet">
<style>
  :root {
    --green: #8cc63f;
    --green-dark: #6fa52b;
    --blue: #0592cd;
    --navy: #0d2a5c;
    --orange: #faa54b;
    --ink: #4a4a4a;
    --paper: #ffffff;
    --backdrop: #e6e6e6;
  }
  * { margin: 0; padding: 0; box-sizing: border-box; }
  html, body { width: 853px; height: 1200px; overflow: hidden; }
  body {
    background: var(--backdrop);
    font-family: "Open Sans", Arial, sans-serif;
    color: var(--ink);
    display: flex;
    flex-direction: column;
    align-items: center;
    justify-content: center;
    gap: 16px;
  }
  .flyer-side {
    position: relative;
    width: 793px;
    height: 562px;
    overflow: hidden;
    background: var(--paper);
    box-shadow: 0 3px 10px rgba(0,0,0,0.18);
  }
  .photo { position: absolute; inset: 0; }
  .photo--golfer {
    background: linear-gradient(180deg, #8fb6d6 0%, #c9d9de 32%, #9bb36a 48%, #6f9a3e 70%, #5b8a34 100%);
  }
  .photo--course {
    background: linear-gradient(180deg, #2f6fb7 0%, #6fa3d6 30%, #c7d6c4 50%, #7ea24a 62%, #4f7d2e 100%);
  }
  .shapes { position: absolute; inset: 0; }

  /* Front */
  .front-copy { position: absolute; left: 34px; top: 232px; width: 320px; }
  .course-title {
    color: var(--green-dark);
    font-size: 27px;
    font-weight: 600;
    line-height: 1.1;
    text-transform: uppercase;
  }
  .course-tagline {
    margin-top: 8px;
    font-size: 12px;
    letter-spacing: 0.5px;
    text-transform: uppercase;
    color: var(--ink);
  }
  .course-intro {
    margin-top: 22px;
    font-size: 12.5px;
    line-height: 1.45;
  }
  .contact { position: absolute; left: 34px; }
  .contact-phone {
    display: flex; align-items: center; gap: 10px;
    font-size: 17px; font-weight: 600; color: var(--navy);
  }
  .contact-web {
    margin-top: 8px;
    font-size: 14px; font-weight: 600; color: var(--blue);
  }
  .front .contact { top: 470px; }
  .brand {
    position: absolute;
    display: flex; align-items: center; gap: 10px;
    color: var(--green-dark);
    font-size: 17px; font-weight: 700; line-height: 1.05;
    text-transform: uppercase;
  }
  .brand-dot {
    width: 28px; height: 28px; border-radius: 50%;
    background: var(--green-dark); flex: none;
  }
  .front .brand { right: 30px; bottom: 32px; }

  /* Back */
  .pass-columns {
    position: absolute; top: 34px; left: 34px;
    display: flex; gap: 18px;
  }
  .pass-card {
    width: 232px; height: 300px;
    background: rgba(13, 42, 92, 0.82);
    color: #fff;
  }
  .pass-card h2 {
    background: rgba(5, 25, 60, 0.85);
    font-size: 15px; font-weight: 700;
    text-align: center; text-transform: uppercase;
    padding: 16px 8px;
  }
  .pass-card ul { list-style: none; padding: 18px 16px; }
  .pass-card li {
    font-size: 12.5px; line-height: 1.4; margin-bottom: 10px;
    padding-left: 12px; position: relative;
  }
  .pass-card li::before { content: "•"; position: absolute; left: 0; }
  .offer { position: absolute; left: 34px; top: 382px; }
  .offer-label {
    color: #fff; font-size: 14px; font-weight: 700; text-transform: uppercase;
    letter-spacing: 0.5px;
  }
  .offer-detail {
    margin-top: 4px;
    color: var(--orange); font-size: 17px; font-weight: 600;
  }
  .back .contact { top: 478px; }
  .back .brand { right: 34px; bottom: 34px; }
</style>
</head>
<body>

<section class="flyer-side front">
  <div class="photo photo--golfer" role="img" aria-label="Photograph of a golfer in a pink shirt playing out of a bunker on a sunny course"></div>
  <svg class="shapes" viewBox="0 0 793 562" width="793" height="562" aria-hidden="true">
    <path d="M0,205 C150,185 290,215 360,290 C425,360 455,470 500,562 L0,562 Z" fill="#ffffff"/>
    <path d="M420,562 C520,465 650,425 793,412 L793,562 Z" fill="#8cc63f"/>
    <path d="M540,562 C610,497 700,468 793,462 L793,562 Z" fill="#ffffff"/>
  </svg>
  <div class="front-copy">
    <h1 class="course-title">Thistle Bank<br>Golf Course</h1>
    <p class="course-tagline">New golf membership passes</p>
    <p class="course-intro">Enjoy golf all year round at one of Australia’s leading courses with our new 2017/18 membership passes. Choose from a variety of pass options to suit every budget.</p>
  </div>
  <div class="contact">
    <div class="contact-phone">
      <svg width="20" height="20" viewBox="0 0 20 20" aria-hidden="true"><circle cx="10" cy="10" r="10" fill="#0592cd"/><path d="M7 5.5l1.6-.4 1 2.4-1 .8a6 6 0 0 0 2.6 2.6l.8-1 2.4 1-.4 1.6c-3.8.6-7.6-3.2-7-7z" fill="#fff"/></svg>
      <span>03 9482 5160</span>
    </div>
    <div class="contact-web">www.thistlebankgolfpark.com.au</div>
  </div>
  <div class="brand"><span class="brand-dot"></span><span>Thistle Bank<br>Golf Course</span></div>
</section>

<section class="flyer-side back">
  <div class="photo photo--course" role="img" aria-label="Photograph of the course with bunkers, fairway and blue sky"></div>
  <svg class="shapes" viewBox="0 0 793 562" width="793" height="562" aria-hidden="true">
    <path d="M0,450 C220,430 520,470 793,440 L793,562 L0,562 Z" fill="#ffffff"/>
  </svg>
  <div class="pass-columns">
    <article class="pass-card">
      <h2>Junior Pass</h2>
      <ul>
        <li>For golfers under 18 years</li>
        <li>Play once a week or more</li>
        <li>Weekday and weekend options</li>
        <li>Great value for young players</li>
      </ul>
    </article>
    <article class="pass-card">
      <h2>Weekday Pass</h2>
      <ul>
        <li>Play Monday to Friday, 18 holes</li>
        <li>Ideal for seniors and shift workers</li>
        <li>Private club quality amenities</li>
      </ul>
    </article>
    <article class="pass-card">
      <h2>7 Day Pass</h2>
      <ul>
        <li>Unlimited golf 7 days per week</li>
        <li>Award winning 18 hole course</li>
        <li>Voted 15th best value course in Australia</li>
      </ul>
    </article>
  </div>
  <div class="offer">
    <div class="offer-label">Payment Options</div>
    <div class="offer-detail">Pay weekly, fortnightly or monthly</div>
  </div>
  <div class="contact">
    <div class="contact-phone">
      <svg width="20" height="20" viewBox="0 0 20 20" aria-hidden="true"><circle cx="10" cy="10" r="10" fill="#0592cd"/><path d="M7 5.5l1.6-.4 1 2.4-1 .8a6 6 0 0 0 2.6 2.6l.8-1 2.4 1-.4 1.6c-3.8.6-7.6-3.2-7-7z" fill="#fff"/></svg>
      <span>03 9482 5160</span>
    </div>
    <div class="contact-web">www.thistlebankgolfpark.com.au</div>
  </div>
  <div class="brand"><span class="brand-dot"></span><span>Thistle Bank<br>Golf Course</span></div>
</section>

</body>
</html>
```